Roofing Company Realtor Marketing Flyer

We would like a design for marketing material aimed at realtors. We are seeking to build relationships with local realtors to ensure that both sellers and buyers are happy and confident with their roofing systems through roof inspections, No-Leak certification, roof repairs, and replacements if necessary.

There are three points that must be included:
1. Home inspectors are generalists. We are roof experts that specialize in diagnosing and fixing roofing problems.
2. We offer "No Leak" certification to offer peace of mind to homeowners.
3. We offer referral bonuses for realtors.

Target Market(s)

Realtors

Industry/Entity Type

Roofing

Font styles to use
Sans Serif

Colors

Designer to choose colors to be used in the design.

Requirements
Must have
• Must be double-sided.
• Must be similar to current marketing materials design. See website http://gablecrestpro.example and attached images for details.
• We would also like a "fanned out" version of our Sample Inspection Report showing glimpses of some of the images on the later pages (See attached documents).

```html
<!DOCTYPE html>
<html lang="en">
<head>
<meta charset="utf-8">
<title>GableCrest Pro – Realtor Flyer</title>
<link href="https://fonts.googleapis.com/css2?family=Lato:wght@400;700&family=Michroma&display=swap" rel="stylesheet">
<style>
  :root{
    --stage:#e9e6e2;
    --slate:#58585a;
    --slate-dark:#4a4a4c;
    --orange:#f0892a;
    --orange-deep:#e8791a;
    --ink:#222;
    --mist:#f1f1f1;
    --white:#fff;
  }
  *{box-sizing:border-box;margin:0;padding:0}
  html,body{width:1200px;height:1200px;overflow:hidden;background:var(--stage)}
  body{position:relative;font-family:"Lato",sans-serif;color:var(--ink)}
  .sheet{position:absolute;top:260px;width:656px;height:850px;transform:scale(.8);transform-origin:0 0;background:var(--white);overflow:hidden;box-shadow:0 4px 14px rgba(0,0,0,.25)}
  .sheet--front{left:47px}
  .sheet--back{left:629px}
  .sheet svg.header-art{position:absolute;left:0;top:0}
  .brand{position:absolute;font-family:"Lato",sans-serif;font-weight:700;font-size:46px;color:var(--white);letter-spacing:.5px;white-space:nowrap}
  .sheet--front .brand{right:32px;top:34px}
  .sheet--back .brand{left:30px;top:46px}
  .hook{position:absolute;font-family:"Michroma",sans-serif;font-size:19px;line-height:25px;letter-spacing:.5px}
  .hook .l1{display:block;padding-left:54px;color:var(--slate)}
  .hook .l2{display:block;color:var(--orange)}
  .front-hook{left:58px;top:106px}
  .value-band{position:absolute;left:0;top:460px;width:656px;height:75px;background:var(--orange);text-align:center;font-family:"Michroma",sans-serif;padding-top:8px}
  .value-band .l1{font-size:19px;color:var(--slate);display:block;line-height:28px}
  .value-band .l2{font-size:21px;color:var(--white);display:block;line-height:32px}
  .service{position:absolute;top:550px;width:142px;text-align:center}
  .service .photo{width:142px;height:117px;border:1px solid #999;box-shadow:0 2px 3px rgba(0,0,0,.3)}
  .service p{font-size:13px;line-height:16px;margin-top:10px;color:var(--ink);margin-left:-20px;margin-right:-20px}
  .checklist{position:absolute;left:0;top:720px;width:656px;height:62px;background:var(--mist);font-size:10.5px;color:var(--ink)}
  .checklist li{position:absolute;list-style:none;padding-left:20px;line-height:13px}
  .checklist svg{position:absolute;left:0;top:0}
  .partner{position:absolute;top:790px;width:656px;text-align:center;color:var(--orange-deep);font-size:15px;font-weight:700}
  .footer{position:absolute;left:0;bottom:0;width:656px;height:32px;background:var(--slate);color:var(--white);font-size:11px;display:flex;justify-content:center;align-items:center;gap:22px}
  .footer span{display:flex;align-items:center;gap:8px}
  .feature{position:absolute;left:31px;width:594px;height:102px}
  .feature .photo{position:absolute;left:0;top:0;width:142px;height:102px;border:1px solid #999;box-shadow:0 2px 3px rgba(0,0,0,.3)}
  .feature h3{position:absolute;left:160px;top:0;font-size:13px;font-weight:700;color:var(--ink)}
  .feature p{position:absolute;left:160px;top:22px;width:435px;font-size:10px;line-height:13px;text-align:justify;color:#333}
  .badge-band{position:absolute;left:0;top:755px;width:656px;height:63px;background:var(--orange)}
  .badge-band svg{position:absolute;left:0;top:0}
</style>
</head>
<body>

<!-- Front side -->
<section class="sheet sheet--front">
  <svg class="header-art" width="656" height="460" viewBox="0 0 656 460">
    <defs>
      <linearGradient id="frontScene" x1="0" y1="0" x2="0" y2="1">
        <stop offset="0" stop-color="#e9f1f8"/>
        <stop offset=".3" stop-color="#8fb3d8"/>
        <stop offset=".55" stop-color="#d9cbb0"/>
        <stop offset=".85" stop-color="#b9a98c"/>
        <stop offset="1" stop-color="#5f8a3e"/>
      </linearGradient>
    </defs>
    <rect width="656" height="460" fill="var(--slate)"/>
    <polygon points="0,160 177,36 345,134 656,134 656,460 0,460" fill="url(#frontScene)" role="img" aria-label="Photo of a large two-storey brick family home with landscaped garden under a blue sky"/>
    <polyline points="0,150 177,24 345,124 656,124" fill="none" stroke="var(--orange)" stroke-width="14" stroke-linejoin="miter"/>
  </svg>
  <div class="brand">GableCrest Pro</div>
  <div class="hook front-hook"><span class="l1">BUYING OR</span><span class="l2">SELLING A HOUSE?</span></div>

  <div class="value-band">
    <span class="l1">We can help You protect your</span>
    <span class="l2">INTERESTS &amp; ADD PROPERTY VALUE</span>
  </div>

  <div class="service" style="left:56px">
    <div class="photo" role="img" aria-label="Roofer inspecting a shingle roof ridge" style="background:linear-gradient(160deg,#8a6a4a,#b4875a 50%,#6e5238)"></div>
    <p>Roof Analysis &amp;<br>NO-LEAK Certification</p>
  </div>
  <div class="service" style="left:254px">
    <div class="photo" role="img" aria-label="Worker repairing damaged roof shingles" style="background:linear-gradient(160deg,#3c3c3e,#7a7676 55%,#9a5a5a)"></div>
    <p>Leak &amp;<br>Damage Repair</p>
  </div>
  <div class="service" style="left:454px">
    <div class="photo" role="img" aria-label="Crew installing a new roof" style="background:linear-gradient(180deg,#6c9bd0,#a8c3e0 45%,#d9d4cc)"></div>
    <p>Roof Replacement</p>
  </div>

  <ul class="checklist">
    <li style="left:34px;top:14px"><svg width="12" height="12" viewBox="0 0 12 12"><rect x="1" y="1" width="10" height="10" fill="none" stroke="var(--orange)" stroke-width="1.3"/><path d="M3 6l2.2 2.2L10 3" fill="none" stroke="var(--orange)" stroke-width="1.5"/></svg>Understand the true detail of the roof.</li>
    <li style="left:34px;top:40px"><svg width="12" height="12" viewBox="0 0 12 12"><rect x="1" y="1" width="10" height="10" fill="none" stroke="var(--orange)" stroke-width="1.3"/><path d="M3 6l2.2 2.2L10 3" fill="none" stroke="var(--orange)" stroke-width="1.5"/></svg>Cover warranty gaps with our "No-Leak" Certification.</li>
    <li style="left:339px;top:14px;width:290px"><svg width="12" height="12" viewBox="0 0 12 12"><rect x="1" y="1" width="10" height="10" fill="none" stroke="var(--orange)" stroke-width="1.3"/><path d="M3 6l2.2 2.2L10 3" fill="none" stroke="var(--orange)" stroke-width="1.5"/></svg>Our expert crews perform the repair and replacement services.</li>
  </ul>

  <p class="partner">Ask us about our partnership program!</p>

  <footer class="footer">
    <span><svg width="11" height="11" viewBox="0 0 12 12"><path d="M2 1l3 .5 1 2.5-1.5 1a7 7 0 0 0 3.5 3.5l1-1.5 2.5 1 .5 3C6 11 1 6 2 1z" fill="var(--orange)"/></svg>844-555-0142</span>
    <span><svg width="11" height="8" viewBox="0 0 12 8"><rect width="12" height="8" fill="var(--orange)"/><path d="M0 0l6 4 6-4" fill="none" stroke="var(--slate)" stroke-width="1"/></svg>info@gablecrestpro.example</span>
    <span><svg width="11" height="11" viewBox="0 0 12 12"><circle cx="6" cy="6" r="5.3" fill="none" stroke="var(--orange)" stroke-width="1.3"/><path d="M.7 6h10.6M6 .7c-3 3-3 7.6 0 10.6M6 .7c3 3 3 7.6 0 10.6" fill="none" stroke="var(--orange)" stroke-width="1"/></svg>www.gablecrestpro.example</span>
  </footer>
</section>

<!-- Back side -->
<section class="sheet sheet--back">
  <svg class="header-art" width="656" height="400" viewBox="0 0 656 400">
    <defs>
      <linearGradient id="backScene" x1="0" y1="0" x2="0" y2="1">
        <stop offset="0" stop-color="#5e95d6"/>
        <stop offset=".35" stop-color="#b7cfe6"/>
        <stop offset=".55" stop-color="#c9b3a8"/>
        <stop offset=".85" stop-color="#a58a78"/>
        <stop offset="1" stop-color="#6f9a4a"/>
      </linearGradient>
    </defs>
    <rect width="656" height="400" fill="var(--slate)"/>
    <polygon points="0,140 300,140 478,38 656,142 656,395 0,395" fill="url(#backScene)" role="img" aria-label="Photo of a two-storey stucco and stone house with a brown shingle roof"/>
    <polyline points="0,130 300,130 478,26 660,132" fill="none" stroke="var(--orange)" stroke-width="14" stroke-linejoin="miter"/>
  </svg>
  <div class="brand">GableCrest Pro</div>

  <article class="feature" style="top:408px">
    <div class="photo" role="img" aria-label="House exterior seen from the lawn" style="background:linear-gradient(180deg,#8fb2d8,#b9a98f 50%,#5b8840)"></div>
    <h3>Understand the true detail of the roof</h3>
    <p>Home inspectors, who are generalists, are often unable to adequately inspect and assess the condition of roofing systems. GableCrest's specialists are trained to diagnose roofing problems and recommend solutions to fit any budget. Our expert Advisors carefully investigate all aspects of the roofing system to assess the condition of the roof. After completing the inspection, our Advisors compile a comprehensive report of their findings including images of the roofing system.</p>
  </article>

  <article class="feature" style="top:523px">
    <div class="photo" role="img" aria-label="Roofer nailing shingles beside a ladder" style="background:linear-gradient(160deg,#4a4a4a,#7b6a60 50%,#8c5a4a)"></div>
    <h3 style="top:17px">Cover warranty gaps with our “No-Leak” Certification</h3>
    <p style="top:40px">Home warranties typically cover appliances, not roofing systems. What good is a warranty if it doesn't protect your property from top to bottom? Our "No-Leak" Certification provides peace of mind to homeowners</p>
  </article>

  <article class="feature" style="top:641px">
    <div class="photo" role="img" aria-label="Hands fitting roof tiles during a repair" style="background:linear-gradient(160deg,#3c64a8,#c9a58a 55%,#b0553c)"></div>
    <h3 style="top:14px">Our expert crews perform the repair &amp; replacement services</h3>
    <p style="top:40px">Repair and replacement services aren't just “jobs” to us. We take pride in every step of the process from quote to completion. Our dedicated office staff coordinates with our production team and technicians to ensure quality work and customer satisfaction.</p>
  </article>

  <div class="badge-band">
    <svg width="656" height="63" viewBox="0 0 656 63" role="img" aria-label="Certification and membership badges">
      <circle cx="102" cy="32" r="24" fill="#4f9a3a"/>
      <circle cx="224" cy="32" r="25" fill="#2f66b0" stroke="var(--white)" stroke-width="2"/>
      <circle cx="338" cy="32" r="25" fill="#2f66b0" stroke="var(--white)" stroke-width="2"/>
      <circle cx="452" cy="32" r="23" fill="#c63030" stroke="var(--white)" stroke-width="2"/>
      <circle cx="572" cy="32" r="24" fill="#d9772a" stroke="#6b3d1a" stroke-width="2"/>
    </svg>
  </div>

  <footer class="footer">
    <span><svg width="11" height="11" viewBox="0 0 12 12"><path d="M2 1l3 .5 1 2.5-1.5 1a7 7 0 0 0 3.5 3.5l1-1.5 2.5 1 .5 3C6 11 1 6 2 1z" fill="var(--orange)"/></svg>844-555-0142</span>
    <span><svg width="11" height="8" viewBox="0 0 12 8"><rect width="12" height="8" fill="var(--orange)"/><path d="M0 0l6 4 6-4" fill="none" stroke="var(--slate)" stroke-width="1"/></svg>info@gablecrestpro.example</span>
    <span><svg width="11" height="11" viewBox="0 0 12 12"><circle cx="6" cy="6" r="5.3" fill="none" stroke="var(--orange)" stroke-width="1.3"/><path d="M.7 6h10.6M6 .7c-3 3-3 7.6 0 10.6M6 .7c3 3 3 7.6 0 10.6" fill="none" stroke="var(--orange)" stroke-width="1"/></svg>www.gablecrestpro.example</span>
  </footer>
</section>

</body>
</html>
```